New website for engineering consultant

We need to update our existing web site. We've just had our logo re-done and have attached it.

We are an engineering consulting firm that specialises in mechanical and structural engineering, design and drafting. Our customers are other businesses in the manufacturing, mining and agricultural industries.

We would like the designs to be professional and highlight that we are innovative.

Industry/Entity Type

Mining

Requirements
Must have
• A module that rotates pictures so we can showcase certain projects. We have attached a few rendered images of projects for you to play with.

```html
<!DOCTYPE html>
<html lang="en">
<head>
<meta charset="utf-8">
<title>TORQ-LINE | Engineering Sustainable Futures</title>
<link href="https://fonts.googleapis.com/css2?family=Ubuntu:wght@400;500&display=swap" rel="stylesheet">
<style>
:root{
  --navy-deep:#031a5c;
  --navy:#0a3a9a;
  --blue-glow:#1b6fd6;
  --panel-border:#2a5fc0;
  --header-bg:#f4f4f4;
  --brand-blue:#1b3aa8;
  --link-blue:#1f57c4;
  --text-light:#e6ecff;
  --purple:#7a3dc0;
  --green:#6cc23a;
  --orange:#ee9415;
  --footer:#0f6fb3;
  --social:#2a7fc4;
  --render-light:#e3db3a;
  --render-dark:#b9ad18;
}
*{box-sizing:border-box;margin:0;padding:0}
html,body{width:1200px;height:1125px;overflow:hidden}
body{
  position:relative;
  font-family:"Ubuntu",sans-serif;
  color:var(--text-light);
  background:radial-gradient(ellipse 700px 520px at 600px 330px,var(--blue-glow) 0%,var(--navy) 45%,var(--navy-deep) 100%);
}
.site-header{position:absolute;left:18px;top:17px;width:1164px;height:135px;background:var(--header-bg)}
.brand{position:absolute;left:18px;top:12px;width:416px;height:110px;background:#fff;border-radius:14px;display:flex;align-items:center;padding-left:22px;gap:18px}
.brand-dot{width:60px;height:60px;border-radius:50%;background:var(--brand-blue)}
.brand-name{font-size:34px;font-weight:500;color:var(--brand-blue);letter-spacing:-0.5px}
.main-nav{position:absolute;left:662px;top:28px;display:flex;gap:40px}
.main-nav a{display:flex;align-items:center;gap:6px;color:var(--link-blue);text-decoration:none;font-size:15px}
.search{position:absolute;left:833px;top:77px;width:278px;height:36px;border:2px solid #b9d3ee;border-radius:18px;background:#fff;display:flex;align-items:center;padding:0 12px 0 16px;justify-content:space-between;color:#555;font-size:14px}
.hero-render{position:absolute;left:312px;top:212px;width:410px;height:225px;border-radius:12px;background:linear-gradient(135deg,var(--render-light),var(--render-dark))}
.hero-title{position:absolute;left:665px;top:216px;font-size:24px;font-weight:400;color:#fff}
.hero-text{position:absolute;left:732px;top:262px;width:360px;font-size:12px;line-height:14.5px;color:#e9efff}
.hero-rule{position:absolute;left:732px;top:312px;width:355px;height:1px;background:linear-gradient(90deg,transparent,#6f9be6,transparent)}
.slide-arrow{position:absolute;width:46px;height:46px}
.slide-prev{left:135px;top:368px}
.slide-next{left:1000px;top:380px}
.content{position:absolute;left:42px;top:497px;width:1116px;height:470px;border:2px solid var(--panel-border);border-radius:18px;background:rgba(8,38,110,.75)}
.showcase-tab{position:absolute;left:917px;top:450px;width:229px;height:90px}
.welcome{position:absolute;left:20px;top:20px;width:1070px}
.welcome h2{font-size:24px;font-weight:400;color:#fff;margin-bottom:14px}
.welcome p{font-size:14px;line-height:17.4px;margin-bottom:17px}
.service{position:absolute;top:222px;width:263px;height:223px;border-radius:14px;padding:14px 16px;color:#fff}
.service h3{position:absolute;font-size:15px;font-weight:400;white-space:nowrap}
.service p{position:absolute;left:16px;right:18px;bottom:22px;font-size:12px;line-height:15px}
.service .more{position:absolute;right:26px;bottom:4px;font-size:12px;color:#1b54e0}
.service .art{position:absolute;border-radius:10px}
.service-engineering{left:115px;background:var(--purple);border:1px solid #5b7be0}
.service-engineering h3{left:97px;top:18px}
.service-engineering .art{left:20px;top:8px;width:70px;height:100px;background:linear-gradient(135deg,#e9ecf5,#9aa6c4)}
.service-specialty{left:419px;background:linear-gradient(#8ed35a,var(--green))}
.service-specialty h3{left:100px;top:22px}
.service-specialty .art{left:14px;top:8px;width:78px;height:110px;background:linear-gradient(#f0e3d4,#c9d4df)}
.service-technology{left:719px;background:var(--orange)}
.service-technology h3{left:16px;top:24px}
.service-technology .art{left:156px;top:14px;width:92px;height:82px;background:linear-gradient(135deg,#d8e2ec,#3a78c8)}
.site-footer{position:absolute;left:58px;top:1010px;width:1103px;height:76px;border-radius:12px;background:linear-gradient(#1a86c8,var(--footer));display:flex;align-items:center;padding:0 30px;font-size:12px;color:#eef6ff}
.social{position:absolute;right:48px;top:22px;display:flex;gap:8px}
.social span{width:33px;height:33px;background:var(--social);border:1px solid #9cc7ec}
</style>
</head>
<body>
<header class="site-header">
  <div class="brand"><span class="brand-dot"></span><span class="brand-name">TORQ-LINE</span></div>
  <nav class="main-nav">
    <a href="#"><svg width="16" height="12" viewBox="0 0 16 12"><path d="M1 1v6h9v4l5-5-5-5v4H3V1z" fill="#3a8fe0"/></svg>Home</a>
    <a href="#"><svg width="16" height="12" viewBox="0 0 16 12"><path d="M1 1v6h9v4l5-5-5-5v4H3V1z" fill="#3a8fe0"/></svg>About Us</a>
    <a href="#"><svg width="16" height="12" viewBox="0 0 16 12"><path d="M1 1v6h9v4l5-5-5-5v4H3V1z" fill="#3a8fe0"/></svg>Projects</a>
    <a href="#"><svg width="16" height="12" viewBox="0 0 16 12"><path d="M1 1v6h9v4l5-5-5-5v4H3V1z" fill="#3a8fe0"/></svg>Contact Us</a>
  </nav>
  <div class="search">This is my new search
    <svg width="20" height="20" viewBox="0 0 20 20"><circle cx="8" cy="8" r="6" fill="none" stroke="#aaa" stroke-width="2.5"/><path d="M12.5 12.5l5 5" stroke="#aaa" stroke-width="3"/></svg>
  </div>
</header>

<div class="hero-render" role="img" aria-label="Rendered image of a featured engineering project"></div>
<h1 class="hero-title">Engineering Sustainable Future</h1>
<p class="hero-text">We offer a broad range of services that are designed to support and nurture manufacturing companies and industries whether you are big or small.</p>
<div class="hero-rule"></div>

<svg class="slide-arrow slide-prev" viewBox="0 0 46 46"><circle cx="23" cy="23" r="22" fill="#1d86cf" stroke="#8fd0f5" stroke-width="2"/><path d="M26 14l-9 9 9 9" fill="none" stroke="#fff" stroke-width="4"/></svg>
<svg class="slide-arrow slide-next" viewBox="0 0 46 46"><circle cx="23" cy="23" r="22" fill="#1d86cf" stroke="#8fd0f5" stroke-width="2"/><path d="M20 14l9 9-9 9" fill="none" stroke="#fff" stroke-width="4"/></svg>

<main class="content">
  <section class="welcome">
    <h2>Welcome</h2>
    <p>TORQ-LINE is a mechanical engineering and technology company focused on helping local manufacturing companies and local industries improve their products, services and sustainability through the application of engineering, technology and focused improvement.</p>
    <p>We offer a broad range of services that are designed to support and nurture manufacturing companies and industries whether you are big or small. We bring togther the services you would only find in a capital city to companies in North Queensland at a competitive rates. Our core services revolve around the application of the latest 3D Solid Modelling technology to assist in creating solutions to your mechanical design problems. These services are complemented by our Technology services which are designed to help your company leverage the latest technology to become globally competitive. Furthermore we offer a range of Focused Im-provement and Specialty services as we strive to bring you complete solutions to your business.</p>
  </section>
  <article class="service service-engineering">
    <div class="art" role="img" aria-label="Drafting compass over blueprint"></div>
    <h3>Engineering &amp; Design</h3>
    <p>We offer a broad range of services that are designed to support and nurture manufacturing companies and industries whether you are big or small. We bring togther the services</p>
    <a class="more">Read More</a>
  </article>
  <article class="service service-specialty">
    <div class="art" role="img" aria-label="Specialist consultant figure"></div>
    <h3>Speciality Services</h3>
    <p>We offer a broad range of services that are designed to support and nurture manufacturing companies and industries whether you are big or small. We bring togther the services</p>
    <a class="more">Read More</a>
  </article>
  <article class="service service-technology">
    <h3>Technology</h3>
    <div class="art" role="img" aria-label="Desktop computer monitor"></div>
    <p>We offer a broad range of services that are designed to support and nurture manufacturing companies and industries whether you are big or small. We bring togther the services</p>
    <a class="more">Read More</a>
  </article>
</main>

<svg class="showcase-tab" viewBox="0 0 229 90">
  <defs><linearGradient id="tabFill" x1="0" y1="0" x2="0" y2="1"><stop offset="0" stop-color="#45bff0"/><stop offset="1" stop-color="#1289d6"/></linearGradient></defs>
  <path d="M0 6Q0 0 8 0L215 8Q224 9 226 18L229 60Q228 74 214 76L6 90Q0 90 0 84Z" fill="url(#tabFill)"/>
  <circle cx="37" cy="46" r="22" fill="#1a7fc8" stroke="#8fd6f7" stroke-width="2"/>
  <path d="M33 36l10 10-10 10" fill="none" stroke="#fff" stroke-width="4"/>
  <text x="78" y="54" font-family="Ubuntu, sans-serif" font-size="18" font-weight="500" fill="#fff">Our showcase</text>
</svg>

<footer class="site-footer">
  Copyright © 2009 TORQ-LINE PTY LTD &nbsp;&nbsp;&nbsp; All Rights Reserved.
  <div class="social"><span></span><span></span><span></span><span></span></div>
</footer>
</body>
</html>
```